Need business card with a logo for a hearing aid sales and audiology business. We have two Hearing Instrument Specialists and one Audiologist on staff. Over 25 years in business. Locally owned and operated. Financing available. Most insurances accepted.

Summit Audio Wellness LLC
48730 W Larchmont, Suite 7
Spokane, WA 99281
509-617-2084
www.summitaudiowell.example

Manager
Tobias Kerrell HIS COHC
License #71829046

Target Market(s)

50yr old + people with a hearing loss.

Industry/Entity Type

Business

Contact Information for Business Card

48730 W Larchmont, Suite 7
Spokane, WA 99281
509-617-2084
www.summitaudiowell.example

Manager
Tobias Kerrell HIS COHC
NLVE #71829046

Font styles to use
Serif
Sans Serif

Requirements
Must have
• Business name, Tobias's name and title(s) and contact information, License #, web address

```html
<!DOCTYPE html>
<html lang="en">
<head>
<meta charset="utf-8">
<title>Summit Audio Wellness – Business Card</title>
<link rel="stylesheet" href="https://fonts.googleapis.com/css2?family=Open+Sans:wght@400;600;700&display=swap">
<style>
  :root {
    --navy: #1f4596;
    --blue: #1466b8;
    --ink: #262626;
    --rule: #c9c9c9;
    --card: #ffffff;
    --backdrop: #e9e7e4;
  }
  * { box-sizing: border-box; margin: 0; padding: 0; }
  html, body {
    width: 1200px; height: 1000px; overflow: hidden;
    background: var(--backdrop);
    font-family: "Open Sans", Arial, sans-serif;
    color: var(--ink);
  }
  .card {
    position: absolute; left: 265px; width: 665px;
    background: var(--card);
    box-shadow: 0 2px 6px rgba(0,0,0,.18);
    overflow: hidden;
  }
  .card--front { top: 73px; height: 397px; }
  .card--back  { top: 532px; height: 396px; }

  .brand { display: flex; align-items: center; gap: 12px; color: var(--navy); font-weight: 600; }
  .brand__dot { border-radius: 50%; background: var(--navy); flex: none; }
  .card--front .brand { position: absolute; right: 32px; top: 88px; font-size: 30px; }
  .card--front .brand__dot { width: 26px; height: 26px; }
  .card--back .brand {
    position: absolute; left: 0; right: 0; top: 166px; justify-content: center; font-size: 40px;
  }
  .card--back .brand__dot { width: 34px; height: 34px; }

  .person { position: absolute; left: 33px; top: 196px; }
  .person__name { font-size: 19px; font-weight: 700; color: var(--navy); letter-spacing: .2px; }
  .person__creds { font-size: 15px; font-weight: 400; color: var(--blue); margin-left: 3px; }
  .person__role { font-size: 15px; margin-top: 1px; }
  .rule { position: absolute; left: 33px; top: 248px; width: 452px; height: 1px; background: var(--rule); }
  .license { position: absolute; left: 33px; top: 268px; font-size: 15px; }

  .contact { position: absolute; right: 32px; top: 238px; text-align: right; font-size: 15px; line-height: 22px; }
  .contact__line { display: flex; justify-content: flex-end; align-items: center; gap: 6px; }
  .contact__line svg { width: 15px; height: 15px; fill: var(--blue); }
  .contact__company { font-weight: 700; margin-top: 5px; }

  .band { position: absolute; left: 0; bottom: 0; width: 665px; height: 28px; }
</style>
</head>
<body>
  <section class="card card--front">
    <div class="brand"><span class="brand__dot"></span>Summit Audio Wellness</div>

    <div class="person">
      <div><span class="person__name">TOBIAS KERRELL</span><span class="person__creds">HIS COHC</span></div>
      <div class="person__role">Manager</div>
    </div>
    <div class="rule"></div>
    <div class="license">License #71829046</div>

    <div class="contact">
      <div class="contact__line">509-617-2084
        <svg viewBox="0 0 16 16" aria-hidden="true"><path d="M1 6c0-2 3-3 7-3s7 1 7 3v1h-3V5.5H4V7H1z"/><path d="M4 8h8l2 5H2z"/></svg>
      </div>
      <div class="contact__line">www.summitaudiowell.example
        <svg viewBox="0 0 16 16" aria-hidden="true"><circle cx="8" cy="8" r="7" fill="none" stroke="currentColor" stroke-width="2" style="stroke:var(--blue)"/><path d="M1 8h14M8 1c-3 4-3 10 0 14M8 1c3 4 3 10 0 14" fill="none" style="stroke:var(--blue)" stroke-width="1.3"/></svg>
      </div>
      <div class="contact__company">Summit Audio Wellness</div>
      <div>48730 W Larchmont, Suite 7</div>
      <div>Spokane, WA 99281</div>
    </div>

    <svg class="band" viewBox="0 0 665 28" preserveAspectRatio="none" aria-hidden="true">
      <polygon points="0,11 335,11 318,28 0,28" fill="var(--navy)"/>
      <polygon points="360,0 665,0 665,28 333,28" fill="var(--blue)"/>
    </svg>
  </section>

  <section class="card card--back">
    <div class="brand"><span class="brand__dot"></span>Summit Audio Wellness</div>
  </section>
</body>
</html>
```